Brookvane Consulting Business Card Design

Business Card Design for Brookvane Consulting. Brookvane Consulting is a boutique consultancy based in Atlanta, GA., that specializes in marketing strategy, organization planning, and leadership development. We provide solutions for small businesses and startups as well as Vantage 300 companies.

http://brookvaneconsulting.com/

Target Market(s)

We provide solutions for small businesses and startups as well as Vantage 300 companies.

Industry/Entity Type

Consulting

Contact Information for Business Card

Two sided business card with priority on contact information, logo, tag line (Guidance to plan bolder, act sooner, grow further)

Colors

Designer to choose colors to be used in the design.

Requirements
Must have
• contact information, logo, tag line (Guidance to plan bolder, act sooner, grow further)
• Simple no over communication.
Nice to have
• I would like to see different placements of logo and creative use of both sides of the card
Should not have
• Do not put too much information on the card.

```html
<!DOCTYPE html>
<html lang="en">
<head>
<meta charset="utf-8">
<title>Brookvane Consulting – Business Card</title>
<link href="https://fonts.googleapis.com/css2?family=Open+Sans:wght@400;600&display=swap" rel="stylesheet">
<style>
  :root {
    --ink: #000000;
    --paper: #ffffff;
    --band: #0d0e10;
    --stage: #e9e7e3;
    --muted: #d8d8d8;
    --shade-dark: #141518;
    --shade-light: #3a3c40;
  }
  html, body {
    margin: 0;
    width: 1200px;
    height: 900px;
    overflow: hidden;
    background: var(--stage);
    font-family: "Open Sans", Arial, sans-serif;
  }
  .canvas {
    position: relative;
    width: 1200px;
    height: 900px;
  }
  .card {
    position: absolute;
    left: 250px;
    width: 700px;
    height: 400px;
    overflow: hidden;
    box-shadow: 0 6px 18px rgba(0,0,0,0.18);
  }
  .card--front { top: 40px; background: var(--paper); }
  .card--back  { top: 460px; background: var(--ink); }

  /* front */
  .brand {
    position: absolute;
    left: 48px;
    top: 150px;
    color: var(--ink);
  }
  .brand__name {
    font-size: 44px;
    font-weight: 600;
    letter-spacing: 0.5px;
    line-height: 1;
    margin: 0;
  }
  .brand__tagline {
    margin: 14px 0 0;
    font-size: 15px;
    font-weight: 600;
    letter-spacing: 0.2px;
  }
  .band {
    position: absolute;
    left: 0;
    bottom: 0;
    width: 100%;
    height: 148px;
    background: var(--band);
  }
  .band__texture {
    position: absolute;
    right: 0;
    top: 0;
    width: 380px;
    height: 100%;
    background: radial-gradient(ellipse at 100% 0%, var(--shade-light) 0%, var(--shade-dark) 55%, var(--band) 80%);
  }
  .contact {
    position: absolute;
    left: 48px;
    top: 28px;
    margin: 0;
    padding: 0;
    list-style: none;
  }
  .contact__item {
    display: flex;
    align-items: center;
    gap: 16px;
    height: 30px;
    color: var(--muted);
    font-size: 13px;
    letter-spacing: 2px;
    text-transform: uppercase;
  }
  .contact__icon { width: 18px; height: 18px; flex: none; }

  /* back */
  .back__texture {
    position: absolute;
    right: 0;
    top: 0;
    width: 360px;
    height: 100%;
    background: radial-gradient(ellipse at 100% 10%, var(--shade-light) 0%, var(--shade-dark) 45%, var(--ink) 75%);
  }
  .back__brand {
    position: absolute;
    left: 0;
    right: 0;
    top: 168px;
    text-align: center;
    color: var(--paper);
    font-size: 46px;
    font-weight: 600;
    letter-spacing: 0.5px;
    margin: 0;
  }
</style>
</head>
<body>
<main class="canvas">

  <section class="card card--front" aria-label="Business card front">
    <div class="brand">
      <p class="brand__name">Brookvane Consulting</p>
      <p class="brand__tagline">Guidance to plan bolder, act sooner, grow further</p>
    </div>
    <div class="band">
      <div class="band__texture" role="img" aria-label="Decorative layered arc pattern in dark grey"></div>
      <ul class="contact">
        <li class="contact__item">
          <svg class="contact__icon" viewBox="0 0 18 18" aria-hidden="true">
            <rect x="1" y="4" width="16" height="11" fill="#ffffff"/>
            <path d="M1 4 L9 10 L17 4" fill="none" stroke="#0d0e10" stroke-width="1.5"/>
          </svg>
          <span>dara@brookvaneconsulting.com</span>
        </li>
        <li class="contact__item">
          <svg class="contact__icon" viewBox="0 0 18 18" aria-hidden="true">
            <path d="M4 2 L7 2 L8 6 L6 7.5 C7 10 8.5 11.5 10.5 12.5 L12 10.5 L16 11.5 L16 14.5 C16 15.5 15 16 14 16 C8 15.5 2.5 10 2 4 C2 3 3 2 4 2 Z" fill="#ffffff"/>
          </svg>
          <span>404-555-0137</span>
        </li>
        <li class="contact__item">
          <svg class="contact__icon" viewBox="0 0 18 18" aria-hidden="true">
            <g fill="none" stroke="#ffffff" stroke-width="1.3">
              <circle cx="9" cy="9" r="7.5"/>
              <ellipse cx="9" cy="9" rx="3.2" ry="7.5"/>
              <line x1="1.5" y1="9" x2="16.5" y2="9"/>
              <line x1="2.8" y1="5" x2="15.2" y2="5"/>
              <line x1="2.8" y1="13" x2="15.2" y2="13"/>
            </g>
          </svg>
          <span>http://brookvaneconsulting.com/home.html</span>
        </li>
      </ul>
    </div>
  </section>

  <section class="card card--back" aria-label="Business card back">
    <div class="back__texture" role="img" aria-label="Decorative layered arc pattern in dark grey"></div>
    <p class="back__brand">Brookvane Consulting</p>
  </section>

</main>
</body>
</html>
```